Business card design needed

Family General Practitioner/ Family Physician.
Logo is the logo of the Noble Guild of Family Healers Oceania
http://kpltw.varendo.example/ImageShelf/marks/pages/NGFHO%20mark_jpg.htm
Updates

Project Deadline Extended
Reason: Just a bit more time to make changes and the weekend for me to look at things closely and to choose. Thanks, Orin

Thanks for all the submissions. So many of them are really works of art. Not one of them are not good. The ones that I am eliminating are the ones that I think are not suitable for me personally only, and because if I don't, it makes it very difficult to decide as many of you are also sending me slight variations of a card. I have just decided to choose a second place card too. Can't thank you all enough. Good luck, Orin. P.S - Working today till 10 pm as the card says :-), so probably won't be able to give a feedback till late Saturday night or Sunday morning here in Sydney, Australia. 

Project Deadline Extended
Reason: Just added a second place to the budget and realised that Australia is ahead of the rest of the world in the time zone (only :-) - don't want to offend anyone or start a debate!! ) , so Monday deadline will mean it will be a weekend for the rest of the world. Just wanted to give everyone more time to submit their best, especially since I will be picking a second card too. Can't thank everyone enough for the submissions. P.S - Not keen on photos on the card.

Industry/Entity Type

Business

Contact Information for Business Card

Dr. Orin Halvey M.B.B.S., F.N.G.F.H.O
Family General Practitioner
Address, timings, phone and fax number on the back.

Requirements
Must have
• Timings
Mon 7 am - 7 pm
Tues 7 am - 12 pm
Wed 7 am - 10 pm
Thurs 7 am - 12 pm
Fri 7 am - 8 pm
Sat 8 am - 10 pm
Sun - Off

```html
<!DOCTYPE html>
<html lang="en">
<head>
<meta charset="utf-8">
<title>Dr. Orin Halvey – Business Card</title>
<link rel="stylesheet" href="https://fonts.googleapis.com/css2?family=Source+Sans+3:wght@400;600;700&display=swap">
<style>
  :root {
    --backdrop: #ece7df;
    --teal: #40b3a2;
    --white: #ffffff;
    --crimson: #a3161b;
    --ink: #1f2a36;
    --address-ink: #2b2b2b;
  }
  * { margin: 0; padding: 0; box-sizing: border-box; }
  html, body { width: 1200px; height: 378px; overflow: hidden; }
  body {
    position: relative;
    background: var(--backdrop);
    font-family: "Source Sans 3", "Myriad Pro", sans-serif;
  }
  .card {
    position: absolute;
    top: 43px;
    width: 540px;
    height: 307px;
    background: var(--teal);
    box-shadow: 0 2px 6px rgba(0,0,0,0.18);
    overflow: hidden;
  }
  .card--front { left: 46px; }
  .card--back { left: 620px; }

  /* Emblem stand-in */
  .emblem {
    position: absolute;
    display: flex;
    align-items: center;
    gap: 8px;
    color: var(--white);
    font-weight: 600;
    line-height: 1.15;
  }
  .emblem__dot {
    flex: 0 0 auto;
    border-radius: 50%;
    border: 2px solid var(--white);
  }
  .card--front .emblem { left: 32px; top: 168px; width: 155px; font-size: 12px; }
  .card--front .emblem__dot { width: 30px; height: 30px; }
  .card--back .emblem { left: 305px; top: 118px; width: 190px; font-size: 14px; }
  .card--back .emblem__dot { width: 38px; height: 38px; }

  /* Front */
  .identity {
    position: absolute;
    left: 217px;
    top: 130px;
    color: var(--white);
  }
  .identity__name {
    font-size: 35px;
    font-weight: 400;
    line-height: 1;
    letter-spacing: -0.2px;
  }
  .identity__creds {
    margin-top: 13px;
    font-size: 12px;
  }
  .identity__role {
    margin-top: 11px;
    font-size: 17px;
  }
  .edge-stripes {
    position: absolute;
    left: 0; right: 0; bottom: 0;
    height: 14px;
    display: block;
  }

  /* Back */
  .hours {
    position: absolute;
    left: 51px;
    top: 48px;
    color: var(--ink);
  }
  .hours__title {
    margin-left: 47px;
    font-size: 22px;
    font-weight: 400;
    margin-bottom: 12px;
  }
  .hours__table { border-collapse: collapse; font-size: 12.5px; }
  .hours__table td { padding: 0; height: 15.5px; line-height: 15.5px; }
  .hours__day { width: 75px; }
  .hours__sep { width: 19px; }
  .contact-band {
    position: absolute;
    left: 0; right: 0; bottom: 0;
    height: 57px;
    background: var(--white);
    color: var(--address-ink);
    font-weight: 700;
    font-size: 12px;
    text-align: center;
    padding-top: 13px;
    line-height: 15px;
  }
</style>
</head>
<body>
  <section class="card card--front" aria-label="Card front">
    <div class="emblem">
      <span class="emblem__dot"></span>
      <span class="emblem__name">Noble Guild of Family Healers Oceania</span>
    </div>
    <div class="identity">
      <h1 class="identity__name">Dr. Orin Halvey</h1>
      <p class="identity__creds">M.B.B.S., F.N.G.F.H.O</p>
      <p class="identity__role">Family General Practitioner</p>
    </div>
    <svg class="edge-stripes" viewBox="0 0 540 14" preserveAspectRatio="none" aria-hidden="true">
      <rect x="0" y="0" width="540" height="3" fill="#ffffff"/>
      <rect x="0" y="3" width="540" height="7" fill="#a3161b"/>
      <rect x="0" y="10" width="540" height="4" fill="#ffffff"/>
    </svg>
  </section>

  <section class="card card--back" aria-label="Card back">
    <div class="hours">
      <h2 class="hours__title">Timing</h2>
      <table class="hours__table">
        <tr><td class="hours__day">Monday</td><td class="hours__sep">:</td><td>7 AM -&nbsp; 7 PM</td></tr>
        <tr><td class="hours__day">Tuesday</td><td class="hours__sep">:</td><td>7 AM - 12 PM</td></tr>
        <tr><td class="hours__day">Wednesday</td><td class="hours__sep">:</td><td>7 AM - 10 PM</td></tr>
        <tr><td class="hours__day">Thursday</td><td class="hours__sep">:</td><td>7 AM - 12 PM</td></tr>
        <tr><td class="hours__day">Friday</td><td class="hours__sep">:</td><td>7 AM -&nbsp; 8 PM</td></tr>
        <tr><td class="hours__day">Saturday</td><td class="hours__sep">:</td><td>8 AM - 10 PM</td></tr>
        <tr><td class="hours__day">Sunday</td><td class="hours__sep">:</td><td>OFF</td></tr>
      </table>
    </div>
    <div class="emblem">
      <span class="emblem__dot"></span>
      <span class="emblem__name">Noble Guild of Family Healers Oceania</span>
    </div>
    <div class="contact-band">
      <p>Level 2, Harbour Walk Arcade, Marren Plaza Centre, Dunmore Hill, NSW 2170</p>
      <p>P: 02 5550 1840 F: 02 5550 1877</p>
    </div>
  </section>
</body>
</html>
```